Web Design Project

Brightfold Publishing owns and operates a large number of editorial websites. These websites provides mostly consumers in the financial services space with information and price comparisons for a particular service.

Brightfold Publishing, as the holding company for each of these sites, currently has no website. We need to build a website targeted towards potential partners for our websites. The idea being that when we start a conversation with a partner, they can view our site and obtain some basic information about who we are.

The structure of the site is to be very simple, containing only a brief description about who we are, our contact details and a list of some of our websites:
• CoverVault.net.au
• MotorPolicyCheck.com.au
• DwellingCoverCheck.com.au
• MedicalCoverCheck.com.au
• LegacyCoverCheck.com.au
• JourneyCoverCheck.com.au
• AnimalCoverCheck.com.au
• PrivateLendingCheck.com.au
• MobileCoolingUnit.com.au
• FixedSavingsYield.com.au
• ThriftyHousehold.com.au
• CoinNana.com.au
• TameYourPlastic.com.au
• PurseMinder.com.au
• ThirdPartyClaimsCoverNational.com.au
• Trade-Cover.com.au
• MotorPolicyProviders.com.au
• MedicalCoverProviders.com.au
• DwellingCoverHub.com
• LegacyCoverHub.com
• EarningsShieldCoverHub.com
• MedicalCoverHub.com
• AnimalCoverHub.com
• PrivateLendingHub.com
• ChargePlasticHub.com
• DwellingLendingHub.com
• RetireNestEgg.net.au

The design of the site should say 'Internet company', 'professional', 'fresh thinking'. The design should not look like a corporate site that you would see from any corporate services business with images of people in suits. We are ultimately an Internet business and there should be a unique feel to the site.

We are open to a suggestion of a colour pallet as the holding company does not have an established logo.

Some sites that we like are:

http://www.quillmarsh-studio.co.uk/#home
http://previewbox00.layoutdock.example/wt_52418/index.html
http://previewbox00.layoutdock.example/wordpress_61942/
http://ponderloop.example/
http://www.brindlux.example/
http://www.tobiasvrankel.example/
http://www.slickfrontdoors.example/Corporate/design-ideas-detail.html?id=4197
http://pairmint.example/
http://orvendal.example/

Reason: Hi all, Apologies, but I need to extend the timeline. One of our key stakeholders is away for the next week. There are a few good designs that we have received to date and there are some tweaks that we would like to see before making a final decision. Thank you to everyone that has submitted designs - Have a great new year. Derek

Reason: Sorry to have to delay the deadline on this, but we did not find anything in the designs really resonated with us. We will have a further think about the existing designs that have been submitted and how we can provide more specific feedback to the designers to make some modifications to the designs.

Target Market(s)

We are targeting insurance companies / brokers that we are talking to. The idea is that we show a professional face to them.

Industry/Entity Type

Financial

Requirements
Must have
• Home Page (possibly integrated with About us details)
Contact Us
Our Sites

```html
<!DOCTYPE html>
<html lang="en">
<head>
<meta charset="utf-8">
<title>Brightfold Publishing</title>
<link rel="stylesheet" href="https://fonts.googleapis.com/css2?family=Roboto:wght@300;400;700&display=swap">
<style>
  :root {
    --brand-green: #7fb32a;
    --link-green: #6a9a1f;
    --ink: #1a1a1a;
    --body-text: #3c3c3c;
    --muted: #8a8a8a;
    --rule: #d9d9d9;
    --panel: #f2f2ee;
    --pill: #1c1c1c;
    --white: #ffffff;
    --leaf: rgba(150, 200, 80, 0.38);
    --soil: rgba(70, 56, 44, 0.42);
  }
  * { box-sizing: border-box; margin: 0; padding: 0; }
  html, body { width: 1200px; height: 1166px; overflow: hidden; background: var(--white); }
  body { position: relative; font-family: "Roboto", Arial, sans-serif; color: var(--body-text); }
  a { color: inherit; text-decoration: none; }

  .site-header { position: absolute; left: 0; top: 0; width: 1200px; height: 110px; border-bottom: 1px solid var(--rule); }
  .brand { position: absolute; left: 50px; top: 46px; font-size: 22px; font-weight: 700; color: var(--brand-green); letter-spacing: 0.2px; }
  .main-nav { position: absolute; top: 43px; right: 28px; display: flex; }
  .main-nav a { display: block; height: 37px; line-height: 37px; padding: 0 25px; font-size: 17px; font-weight: 300; color: var(--ink); border-radius: 19px; }
  .main-nav a.is-active { background: var(--pill); color: var(--white); padding: 0 34px; margin-right: 4px; }

  .hero { position: absolute; left: 0; top: 110px; width: 1200px; height: 505px; border-bottom: 1px solid var(--rule); }
  .hero-title { position: absolute; left: 0; top: 10px; width: 1200px; text-align: center; font-size: 33px; font-weight: 300; line-height: 41px; color: var(--muted); }
  .hero-title strong { font-weight: 400; color: var(--ink); }
  .hero-visual { position: absolute; left: 216px; top: 100px; width: 702px; height: 336px;
    background:
      radial-gradient(ellipse 48% 16% at 50% 82%, var(--soil) 0%, rgba(70,56,44,0) 100%),
      radial-gradient(ellipse 46% 44% at 56% 52%, var(--leaf) 0%, rgba(150,200,80,0) 100%); }
  .hero-arrow { position: absolute; top: 252px; width: 28px; height: 44px; }
  .hero-arrow.prev { left: 32px; }
  .hero-arrow.next { right: 38px; }

  .about { position: absolute; left: 36px; top: 643px; width: 670px; }
  .section-head { height: 42px; background: var(--panel); border-bottom: 1px solid var(--rule); position: relative; }
  .about .section-head { width: 310px; }
  .section-icon { position: absolute; left: 0; top: -2px; width: 56px; height: 46px; background: linear-gradient(135deg, #c9cfd6, #8c96a0); border-radius: 4px; }
  .section-head h2 { position: absolute; left: 59px; top: 10px; font-size: 20px; font-weight: 400; color: var(--ink); }
  .about-text { margin-top: 20px; padding-left: 4px; width: 672px; font-size: 13px; line-height: 29px; font-weight: 400; color: var(--body-text); }
  .read-more { position: absolute; left: 574px; top: 281px; height: 20px; line-height: 20px; padding: 0 11px; background: var(--pill); color: var(--white); font-size: 12px; border-radius: 10px; }

  .weblinks { position: absolute; left: 810px; top: 643px; width: 311px; height: 291px; background: var(--panel); }
  .weblinks .section-head { width: 311px; }
  .weblinks .section-icon { left: 2px; top: 2px; width: 46px; height: 46px; background: linear-gradient(135deg, #e4e4e4, #9a9a9a); border-radius: 50%; }
  .weblinks .section-head h2 { left: 55px; top: 9px; }
  .sort-toggle { position: absolute; right: 30px; top: 12px; }
  .link-list { position: absolute; left: 10px; top: 60px; width: 291px; list-style: none; border: 1px dashed #b8b8b0; }
  .link-list li { position: relative; height: 35px; line-height: 35px; padding-left: 34px; font-size: 13.5px; color: var(--link-green); border-top: 1px dashed #c4c4bc; }
  .link-list li:first-child { border-top: 0; }
  .link-list li::before { content: ""; position: absolute; left: 9px; top: 14px; width: 7px; height: 7px; border-radius: 50%; background: var(--brand-green); }

  .site-footer { position: absolute; left: 0; top: 988px; width: 1200px; height: 178px; border-top: 1px solid var(--rule); }
  .address { position: absolute; left: 62px; top: 19px; font-style: normal; font-size: 13px; line-height: 17px; color: var(--muted); font-weight: 300; }
  .address .company { color: var(--link-green); font-weight: 400; }
  .social { position: absolute; left: 67px; top: 124px; display: flex; gap: 11px; }
  .social span { width: 32px; height: 32px; border-radius: 50%; background: radial-gradient(circle at 40% 35%, #b5dc6a, #6e9f24); box-shadow: 0 1px 2px rgba(0,0,0,0.3); }
  .footer-nav { position: absolute; right: 38px; top: 27px; display: flex; gap: 41px; font-size: 14px; font-weight: 300; color: #444; }
  .footer-nav a.is-active { color: var(--link-green); }
  .subscribe { position: absolute; left: 846px; top: 97px; display: flex; }
  .subscribe-input { width: 270px; height: 26px; border: 1px solid #c8c8c8; border-right: 0; border-radius: 13px 0 0 13px; padding-left: 12px; font-size: 13px; line-height: 24px; color: #666; font-weight: 300; }
  .subscribe-go { width: 46px; height: 26px; background: var(--pill); color: var(--white); font-size: 13px; line-height: 26px; text-align: center; }
  .copyright { position: absolute; right: 25px; top: 145px; font-size: 13px; font-weight: 300; color: #666; }
</style>
</head>
<body>
  <header class="site-header">
    <div class="brand">Brightfold Publishing</div>
    <nav class="main-nav">
      <a class="is-active" href="#">Home</a>
      <a href="#">About us</a>
      <a href="#">Services</a>
      <a href="#">Solutions</a>
      <a href="#">Careers</a>
      <a href="#">Contact us</a>
    </nav>
  </header>

  <section class="hero">
    <h1 class="hero-title">We specialise in <strong>attracting customers</strong> from our<br>directory of <strong>more than 100 sites to our network</strong> of trusted partners</h1>
    <div class="hero-visual" role="img" aria-label="Three seedlings of increasing size growing from mounds of dark soil"></div>
    <svg class="hero-arrow prev" viewBox="0 0 28 44" aria-label="Previous slide"><polyline points="22,4 6,22 22,40" fill="none" stroke="#111" stroke-width="6" stroke-linecap="round" stroke-linejoin="round"/></svg>
    <svg class="hero-arrow next" viewBox="0 0 28 44" aria-label="Next slide"><polyline points="6,4 22,22 6,40" fill="none" stroke="#111" stroke-width="6" stroke-linecap="round" stroke-linejoin="round"/></svg>
  </section>

  <section class="about">
    <div class="section-head">
      <div class="section-icon" role="img" aria-label="Icon of two people"></div>
      <h2>About us</h2>
    </div>
    <p class="about-text">Lorem ipsum dolor sit amet, consectetuer adipiscing elit, sed diam nonummy nibh euismod tincidunt ut laoreet dolore magna aliquam erat volutpat. Ut wisi enim ad minim veniam, quis nostrud exerci tation ullamcorper suscipit lobortis nisl ut aliquip ex ea commodo consequat.<br>Duis autem vel eum iriure dolor in hendrerit in vulputate velit esse molestie consequat, vel illum dolore eu feugiat nulla facilisis at vero eros et accumsan et iusto odio dignissim qui blandit praesent luptatum zzril delenit augue duis dolore te feugait nulla facilisi. Nam liber tempor cum soluta nobis eleifend option congue nihil imperdiet doming id quod mazim placerat facer possim assum.</p>
    <a class="read-more" href="#">Read more</a>
  </section>

  <aside class="weblinks">
    <div class="section-head">
      <div class="section-icon" role="img" aria-label="Chain link icon"></div>
      <h2>Weblinks</h2>
      <svg class="sort-toggle" width="10" height="16" viewBox="0 0 10 16" aria-hidden="true"><polygon points="5,1 9,6 1,6" fill="#aaa"/><polygon points="1,10 9,10 5,15" fill="#aaa"/></svg>
    </div>
    <ul class="link-list">
      <li>CoverVault.net.au</li>
      <li>MotorPolicyCheck.com.au</li>
      <li>DwellingCoverCheck.com.au</li>
      <li>MedicalCoverCheck.com.au</li>
      <li>LegacyCoverCheck.com.au</li>
      <li>JourneyCoverCheck.com.au</li>
    </ul>
  </aside>

  <footer class="site-footer">
    <address class="address">
      <span class="company">Brightfold Publishing Pty Ltd</span><br>
      Suite 412<br>
      18 Larkfield Lane<br>
      Marlow Heights NSW &nbsp; 2099<br>
      Tel: 02 5550 1384
    </address>
    <div class="social" aria-label="Social links"><span></span><span></span><span></span></div>
    <nav class="footer-nav">
      <a class="is-active" href="#">Home</a>
      <a href="#">About us</a>
      <a href="#">Services</a>
      <a href="#">Solutions</a>
      <a href="#">Careers</a>
      <a href="#">Contact us</a>
    </nav>
    <div class="subscribe">
      <div class="subscribe-input">Email address for subscribe you</div>
      <div class="subscribe-go">Go</div>
    </div>
    <div class="copyright">Copyright © -2011 Brightfold Publishing Pty Ltd</div>
  </footer>
</body>
</html>
```